MOVIE POSTER - THRILLER/SUSPENSE - FEATURE FILM

We need a "coming soon" poster. We prefer that the final file is delivered as a photoshop file or similar so we can edit cast/crew/etc. once that information is available. For now, it can just say COMING SOON.

TITLE OF THE MOVIE: Quiet Roads Of Marrow
TAGLINE: Seeing the future can't save you.
We are open to creative ideas on a cool font.
STORYLINE: QUIET ROADS OF MARROW is a suspenseful story laced with mystery. A woman named Wren witnesses a crime and flees the scene, wrecking her car as she escapes. Days later at the hospital, Wren awakens from a coma but has no recollection of the events that put her there. However, she is having some very strange aftereffects.... when the doctors brought her back from the brink of death, she brought back a little something extra: She's having visions of her future kidnapping and murder! It's a race against the clock as Wren tries to figure out who she can trust and who is trying to kill her. The most important question of all is: Can she solve her own murder before it happens and save herself?

SIZE: 30" x 40" - 300dpi

Elements you can include (but are not required):
Handgun
blonde female (long hair), but don't show the face
darker hair male, but don't show the face
1970 Ravenna (not a main component, but could be background) (black)
missing person flier

MOOD IDEAS:
mystery
thriller
suspense
bad guys/local thugs/mafia type/not dressed well though/more street type

I like the finish style which gives posters a slight unpolished look to it (so it's more like a drawing almost, and not a glossy photograph). Here are a couple examples of the finish that I am talking about:
http://www.reelplakat.com/2015/broken_ridge_ver4.html
http://www.reelplakat.com/2015/cobalt_quartet_ver5.html

Here was a rough mock-up I put together but by no means what we want. It was just to create a mood and feel.
http://glimmerbark.com/images/PosterQuietRoads.jpg

Here are a few posters that we like:
http://www.reelplakat.com/2010/hollow_creek.html
http://www.reelplakat.com/2001/coral_tide_ver6.html
http://www.reelplakat.com/2001/iron_keep_ver1.html
http://www.reelplakat.com/2004/mesquite_ver2.html
http://www.reelplakat.com/2008/ride_past_the_grey_edge.html
These are just a few ideas, but we are open to original ideas.

Please feel free to ask questions! We look forward to working with you.

Industry/Entity Type

Movie

Requirements
Must have
• Information and examples are in the "project description."
Nice to have
Should not have

```html
<!DOCTYPE html>
<html lang="en">
<head>
<meta charset="utf-8">
<title>Quiet Roads Of Marrow — Coming Soon</title>
<link rel="stylesheet" href="https://fonts.googleapis.com/css2?family=League+Gothic&family=Montserrat:wght@300&display=swap">
<style>
  :root {
    --backdrop: #e9e8e6;
    --blood: #b0120f;
    --blood-deep: #6e0606;
    --blood-dark: #3f0303;
    --paper: #ffffff;
    --paper-shade: #f1f0ee;
    --ink: #2a2a2a;
  }
  html, body {
    margin: 0;
    width: 1200px;
    height: 1148px;
    overflow: hidden;
    background: var(--backdrop);
  }
  .poster {
    position: absolute;
    left: 187px;
    top: 24px;
    width: 826px;
    height: 1100px;
    overflow: hidden;
    background:
      radial-gradient(ellipse at 45% 35%, var(--blood) 0%, var(--blood-deep) 70%, var(--blood-dark) 100%);
  }
  .poster__art {
    position: absolute;
    inset: 0;
    width: 826px;
    height: 1100px;
  }
  .figure-silhouette {
    position: absolute;
    left: 124px;
    top: 44px;
    width: 266px;
    height: 716px;
    border-radius: 90px 90px 0 0;
    background: linear-gradient(180deg, var(--paper) 0%, var(--paper-shade) 100%);
  }
  .tagline {
    position: absolute;
    left: 413px;
    top: 84px;
    width: 310px;
    margin: 0;
    font-family: "League Gothic", "Oswald", sans-serif;
    font-size: 19px;
    letter-spacing: 0.5px;
    color: var(--paper);
    text-transform: uppercase;
    white-space: nowrap;
  }
  .title {
    position: absolute;
    left: 480px;
    top: 112px;
    width: 250px;
    height: 610px;
    margin: 0;
  }
  .title text {
    font-family: "League Gothic", "Oswald", sans-serif;
    font-size: 170px;
    fill: var(--paper);
  }
  .release-note {
    position: absolute;
    left: 115px;
    top: 858px;
    width: 640px;
    margin: 0;
    font-family: "Montserrat", sans-serif;
    font-weight: 300;
    font-size: 18px;
    letter-spacing: 25px;
    color: var(--ink);
    white-space: nowrap;
  }
</style>
</head>
<body>
  <main class="poster">
    <svg class="poster__art" viewBox="0 0 826 1100" aria-hidden="true">
      <polygon fill="#ffffff"
        points="0,742 40,738 80,746 130,736 190,744 250,735 320,742 380,734 450,743 520,737 590,745 660,736 720,744 780,738 826,742
                826,960 790,968 740,958 690,972 630,962 560,975 500,963 430,970 370,960 300,974 240,962 170,971 110,961 50,970 0,962"/>
    </svg>

    <div class="figure-silhouette" role="img" aria-label="White silhouette of a long-haired woman in profile, holding a handgun at her side"></div>

    <p class="tagline">Seeing the future can't save you.</p>

    <h1 class="title" aria-label="Quiet Roads Of Marrow">
      <svg viewBox="0 0 250 610" width="250" height="610" aria-hidden="true">
        <text x="0" y="145" textLength="230" lengthAdjust="spacingAndGlyphs">QUIET</text>
        <text x="0" y="300" textLength="240" lengthAdjust="spacingAndGlyphs">ROADS</text>
        <text x="110" y="455">OF</text>
        <text x="0" y="605" textLength="250" lengthAdjust="spacingAndGlyphs">MARROW</text>
      </svg>
    </h1>

    <p class="release-note">COMING SOON . . .</p>
  </main>
</body>
</html>
```